I need a business card to give to prospective clients. I am a freelance photographer who photographs most things (except weddings and social stuff) including nature, wildlife and interiors.
I want to look modern and stylish.
I am including a photograph although I am by no means certain that it should be used - what do you think?
More of my images can be seen and downloaded at my PixVault page - just search for Maren Tolbeck
Target Market(s)
Home owners selling or letting properties, private individuals wanting to buy prints
Industry/Entity Type
Business
Contact Information for Business Card
Maren Tolbeck Photography
Maren
Wrenfield Cottage, Mossbank Road, Pelsworth, Carrow Heath, KX41 2RB
Tel: +44 7000 418263. Email: maren@tolbeckstudio.example

```html
<!DOCTYPE html>
<html lang="en">
<head>
<meta charset="utf-8">
<title>Maren Tolbeck Photography – Business Card</title>
<link rel="stylesheet" href="https://fonts.googleapis.com/css2?family=Cinzel:wght@400;600&family=Didact+Gothic&display=swap">
<style>
  :root {
    --backdrop: #2b2b2c;
    --card: #1f1d1e;
    --card-edge: #151414;
    --title: #e9e7e8;
    --text: #bdbbbc;
    --icon: #a9a7a8;
    --accent: #c4161c;
  }
  * { box-sizing: border-box; margin: 0; padding: 0; }
  html, body {
    width: 1200px; height: 900px; overflow: hidden;
    background: var(--backdrop);
  }
  .card {
    position: absolute;
    left: 100px; top: 165px;
    width: 1000px; height: 570px;
    background: linear-gradient(160deg, #252324 0%, var(--card) 55%, var(--card-edge) 100%);
    box-shadow: 0 18px 40px rgba(0,0,0,.45);
  }
  .brand {
    position: absolute;
    left: 160px; top: 150px;
    width: 680px;
    text-align: center;
  }
  .brand-name {
    font-family: 'Cinzel', serif;
    font-weight: 400;
    font-size: 38px;
    letter-spacing: 2px;
    color: var(--title);
    white-space: nowrap;
  }
  .services {
    margin-top: 18px;
    font-family: 'Cinzel', serif;
    font-weight: 600;
    font-size: 22px;
    letter-spacing: 2px;
    color: var(--title);
  }
  .services .divider { color: var(--accent); margin: 0 6px; font-weight: 400; }
  .contact {
    position: absolute;
    left: 160px; top: 380px; right: 90px;
    font-family: 'Didact Gothic', sans-serif;
    font-size: 24px;
    color: var(--text);
  }
  .contact-row { display: flex; align-items: center; gap: 14px; margin-bottom: 18px; }
  .contact-row.split { justify-content: space-between; }
  .contact-item { display: flex; align-items: center; gap: 14px; }
  .icon { width: 26px; height: 22px; fill: var(--icon); flex: none; }
  .address-continued { margin-left: 228px; margin-top: -10px; }
</style>
</head>
<body>
  <div class="card">
    <div class="brand">
      <div class="brand-name">MAREN TOLBECK PHOTOGRAPHY</div>
      <div class="services">
        Nature<span class="divider">|</span>Wildlife<span class="divider">|</span>Interiors
      </div>
    </div>

    <div class="contact">
      <div class="contact-row split">
        <div class="contact-item">
          <svg class="icon" viewBox="0 0 26 22" aria-hidden="true">
            <path d="M1 7c0-3 5-5 12-5s12 2 12 5v2h-6V6H7v3H1z"/>
            <path d="M6 10h14l3 10H3z"/>
          </svg>
          <span class="phone">+44 7000 418263</span>
        </div>
        <div class="contact-item">
          <svg class="icon" viewBox="0 0 26 22" aria-hidden="true">
            <path d="M1 3h24v16H1z M3 5v1l10 7 10-7V5z" fill-rule="evenodd"/>
          </svg>
          <span class="email">maren@tolbeckstudio.example</span>
        </div>
      </div>
      <div class="contact-row">
        <svg class="icon" viewBox="0 0 26 22" aria-hidden="true">
          <path d="M13 1L1 11h3v10h7v-6h4v6h7V11h3z"/>
        </svg>
        <span class="address">Wrenfield Cottage, Mossbank Road, Pelsworth,</span>
      </div>
      <div class="address-continued">Carrow Heath, KX41 2RB</div>
    </div>
  </div>
</body>
</html>
```